Automotive eCommerce Business looking for a business card design

Looking for a clean and simple business card design. Our company name is "Brindle Auto" and we are a company specializing in the ecommerce sales of automotive parts, specifically for pick up trucks and large SUVs. Our company colours are red, black, and white.

Feel free to use the logo provided or create a new logo that you seem fit. Looking forward to your creative ideas!

Industry/Entity Type

Automotive

Contact Information for Business Card

We were thinking of a possibly two-sided design featuring just the logo and company name on one side, and personal information on the other side. Single sided designs will be considered as well.

Font styles to use
Serif
Sans Serif
Decorative

Colors
ec1f27
ffffff
000000

Requirements
Must have
• Space for employee's name, title, phone number and email address, along with the company address and website somewhere.

```html
<!DOCTYPE html>
<html lang="en">
<head>
<meta charset="utf-8">
<title>Brindle Auto Ltd. – Business Card</title>
<link rel="stylesheet" href="https://fonts.googleapis.com/css2?family=Cinzel:wght@400;600&family=Roboto:wght@400&display=swap">
<style>
  :root {
    --backdrop: #1f1f1f;
    --paper: #f1f1f1;
    --brand-red: #9b1c20;
    --band-grey: #555555;
    --ink: #454545;
    --white: #ffffff;
    --faint-red: rgba(155, 28, 32, 0.08);
  }
  * { margin: 0; padding: 0; box-sizing: border-box; }
  html, body { width: 1200px; height: 960px; overflow: hidden; background: var(--backdrop); }
  .canvas { position: relative; width: 1200px; height: 960px; }

  .card { position: absolute; width: 600px; height: 343px; overflow: hidden; box-shadow: 0 2px 6px rgba(0,0,0,0.5); }

  /* Front */
  .card--front { left: 314px; top: 113px; background: var(--paper); }
  .front__decor { position: absolute; left: 300px; top: 120px; width: 300px; height: 300px; border-radius: 50%; background: var(--faint-red); }
  .front__band { position: absolute; left: 0; top: 36px; width: 600px; height: 111px; background: var(--brand-red); }
  .front__band-grey { position: absolute; left: 0; top: 0; width: 106px; height: 111px; background: var(--band-grey); }
  .front__mark { position: absolute; left: 78px; top: 36px; width: 104px; height: 104px; background: var(--white); }
  .company-name { font-family: 'Cinzel', serif; font-weight: 600; letter-spacing: 0.5px; }
  .front__company { position: absolute; left: 38px; top: 154px; font-size: 19px; color: var(--band-grey); }
  .person { position: absolute; right: 80px; top: 66px; text-align: right; color: var(--white); font-family: 'Cinzel', serif; }
  .person__name { font-size: 22px; line-height: 26px; }
  .person__title { font-size: 15px; line-height: 18px; letter-spacing: 0.5px; }

  .contact-list { position: absolute; left: 38px; top: 238px; list-style: none; font-family: 'Roboto', sans-serif; font-size: 14px; color: var(--ink); }
  .contact-list li { display: flex; align-items: center; height: 19px; }
  .contact-list svg { width: 14px; height: 14px; margin-right: 9px; fill: var(--brand-red); }

  .address { position: absolute; left: 391px; top: 255px; font-family: 'Roboto', sans-serif; font-size: 14px; line-height: 19px; color: var(--ink); font-style: normal; }

  /* Back */
  .card--back { left: 311px; top: 472px; background: var(--brand-red); text-align: center; }
  .back__mark { position: absolute; left: 242px; top: 68px; width: 116px; height: 116px; background: var(--paper); }
  .back__company { position: absolute; left: 0; right: 0; top: 230px; font-size: 25px; color: var(--paper); }
  .back__web { position: absolute; left: 0; right: 0; top: 291px; font-family: 'Roboto', sans-serif; font-size: 14px; letter-spacing: 5px; color: var(--paper); }
</style>
</head>
<body>
<main class="canvas">
  <section class="card card--front">
    <div class="front__decor"></div>
    <div class="front__band"><div class="front__band-grey"></div></div>
    <div class="front__mark"></div>
    <p class="front__company company-name">Brindle Auto Ltd.</p>
    <div class="person">
      <p class="person__name">Marcus Hale</p>
      <p class="person__title">CEO/Founder</p>
    </div>
    <ul class="contact-list">
      <li><svg viewBox="0 0 16 16"><path d="M3 1l3 3-1.5 2a9 9 0 0 0 5.5 5.5L12 10l3 3-2 2C7 15 1 9 1 3z"/></svg>604 218 7731</li>
      <li><svg viewBox="0 0 16 16"><path d="M4 0h8v16H4zM5.5 2v10h5V2zM7 13h2v2H7z" fill-rule="evenodd"/></svg>604 559 1287</li>
      <li><svg viewBox="0 0 16 16"><path d="M4 1h8v4H4zM1 6h14v6h-2v3H3v-3H1zM5 10v4h6v-4z" fill-rule="evenodd"/></svg>604 730 4462</li>
      <li><svg viewBox="0 0 16 16"><path d="M1 4h14v9H1zM1 4l7 5 7-5"/></svg>parts@brindleauto.com</li>
    </ul>
    <address class="address">
      2140 Cedar Hollow Road<br>
      Fairbanks, Alaska 99701<br>
      www.brindleauto.com
    </address>
  </section>

  <section class="card card--back">
    <div class="back__mark"></div>
    <p class="back__company company-name">Brindle Auto Ltd.</p>
    <p class="back__web">www.brindleauto.com</p>
  </section>
</main>
</body>
</html>
```